Website for a new t-shirt company called bolddawnapperal.com

We are looking for a talented web designer to create a website that aligns with our brand's message and identity centered around the theme of "Bold Dawn." The website should be modern, clean, and visually appealing while also being user-friendly and easy to navigate.

We will be using the Big Commerce platform for our online store section, so the designer should have experience in designing websites on this platform.

We would like the website to have the following elements:

A color scheme that aligns with the brand's identity and message
A homepage that showcases our products and message, with clear calls-to-action for visitors to explore further
A blog section that highlights our brand's philosophy and offers advice and tips for people looking to make positive changes in their lives
An "About Us" section that introduces our brand and team and offers insight into our mission and values
A contact form that allows visitors to easily get in touch with us for inquiries or support
We are open to creative suggestions and ideas from the designer, but we would like the website to have a modern and minimalist aesthetic that resonates with our target audience of 20 to 40-year-olds.

```html
<!DOCTYPE html>
<html lang="en">
<head>
<meta charset="utf-8">
<title>Bold Dawn — T-Shirts</title>
<link href="https://fonts.googleapis.com/css2?family=Poppins:wght@300;400;500;600;700&display=swap" rel="stylesheet">
<style>
:root{
  --blue:#1a7fe4;
  --blue-dark:#0f4fa6;
  --teal:#47c7d2;
  --ink:#1d1d1f;
  --text:#333;
  --muted:#777;
  --line:#e3e3e3;
  --band:#f5f5f5;
  --deal:#cfcac4;
  --footer:#1f1f21;
  --footer-bottom:#141416;
  --white:#fff;
}
*{margin:0;padding:0;box-sizing:border-box}
html,body{width:1200px;height:5357px;overflow:hidden}
body{font-family:'Poppins',sans-serif;color:var(--text);background:var(--white);position:relative}
.abs{position:absolute}
.photo{position:absolute}
.topbar{position:absolute;top:0;left:0;width:1200px;height:50px;font-size:15px;color:#444}
.topbar .contact{position:absolute;left:144px;top:15px;display:flex;gap:22px;align-items:center}
.topbar .contact span{display:flex;align-items:center;gap:6px}
.topbar .welcome{position:absolute;right:90px;top:15px}
.topbar .welcome a{color:var(--blue);text-decoration:none;font-weight:500}
.nav{position:absolute;top:50px;left:0;width:1200px;height:85px;border-top:1px solid var(--line)}
.brand{position:absolute;left:140px;top:24px;font-size:30px;font-weight:600;color:var(--ink);letter-spacing:-.5px}
.menu{position:absolute;left:340px;top:32px;display:flex;gap:28px;font-size:15px;color:#333}
.menu .active{color:var(--blue)}
.search{position:absolute;left:874px;top:29px;width:170px;height:29px;border:1px solid #ccc;display:flex;align-items:center;gap:6px;padding-left:10px;font-size:14px;color:#555}
.cart{position:absolute;left:1068px;top:30px}
.cart b{position:absolute;top:-8px;right:-8px;width:16px;height:16px;border-radius:50%;background:var(--blue);color:#fff;font-size:10px;text-align:center;line-height:16px}
.hero{position:absolute;top:135px;left:0;width:1200px;height:635px;background:var(--teal)}
.hero .photo{left:686px;top:0;width:514px;height:635px;background:linear-gradient(160deg,#5fd1db,#e9b07e 45%,#f08a4a 70%,#47c7d2)}
.hero .kicker{position:absolute;left:146px;top:228px;font-size:15px;color:#fff;letter-spacing:.3px}
.hero h1{position:absolute;left:146px;top:258px;font-size:52px;line-height:63px;font-weight:700;color:#fff}
.btn-white{position:absolute;left:146px;top:406px;width:154px;height:46px;background:#fff;color:var(--blue);font-size:15px;font-weight:600;text-align:center;line-height:46px}
.features{position:absolute;top:755px;left:146px;width:950px;height:129px;background:#fff;box-shadow:0 6px 24px rgba(0,0,0,.09);display:flex;align-items:center}
.feature{flex:1;display:flex;align-items:center;gap:14px;padding-left:30px;border-right:1px solid var(--line);height:44px}
.feature:last-child{border-right:0}
.feature h4{font-size:17px;font-weight:500;color:#222}
.feature p{font-size:13px;color:var(--muted)}
.coll-text .label{position:absolute;left:179px;top:1330px;font-size:18px;color:var(--blue)}
.coll-text h2{position:absolute;left:179px;top:1356px;font-size:29px;font-weight:500;color:#111}
.coll-text p{position:absolute;left:179px;top:1406px;width:440px;font-size:14.5px;line-height:22px;color:#333}
.btn-outline{position:absolute;left:179px;top:1516px;width:110px;height:32px;border:1px solid #bbb;font-size:12px;font-weight:500;text-align:center;line-height:30px;color:#333}
.section-title{position:absolute;left:0;width:1200px;text-align:center;font-size:30px;font-weight:500;color:#111}
.tabs{position:absolute;top:1686px;left:0;width:1200px;display:flex;justify-content:center;gap:42px;font-size:16px;font-weight:500;color:#222}
.tabs .on{color:var(--blue);border-bottom:2px solid var(--blue);padding:0 6px 6px}
.product{position:absolute;width:202px}
.product .photo{position:relative;width:202px;height:304px}
.product .cat{margin-top:20px;font-size:13px;color:#777;letter-spacing:1px}
.product .name{font-size:15px;font-weight:600;color:#111;margin-top:2px}
.product .price{font-size:15px;font-weight:600;color:var(--blue);margin-top:2px}
.product .price s{color:#888;font-weight:500}
.badge{position:absolute;top:20px;left:14px;width:42px;height:42px;border-radius:50%;background:var(--blue);color:#fff;font-size:12px;line-height:13px;text-align:center;padding-top:8px}
.promo{position:absolute;left:154px;top:2627px;width:878px;height:295px;display:flex}
.promo .left{width:440px;height:295px;background:linear-gradient(135deg,#1652a6,#1e5bb6 50%,#123f86);color:#fff;text-align:center;padding-top:70px}
.promo .left .big{font-size:34px;font-weight:700}
.promo .left .big small{font-size:12px;vertical-align:middle}
.promo .left .sub{font-size:28px;font-weight:600;line-height:36px}
.promo .right{flex:1;background:linear-gradient(90deg,#3a86dc,#5c98d9 60%,#6f9fd0);color:#fff;padding:98px 0 0 46px;font-size:33px;font-weight:500;line-height:43px}
.deal{position:absolute;top:3016px;left:0;width:1200px;height:468px;background:var(--deal)}
.deal .photo{left:0;top:0;width:624px;height:468px;background:linear-gradient(90deg,#ece9e4,#dcd7d1)}
.deal .kicker{position:absolute;left:655px;top:78px;font-size:16px;color:#222}
.deal h2{position:absolute;left:655px;top:104px;font-size:46px;font-weight:700;color:#111}
.deal .pct{position:absolute;left:655px;top:178px;font-size:50px;font-weight:700;color:var(--blue)}
.deal .pct sup{font-size:12px;background:var(--blue);color:#fff;padding:1px 6px;border-radius:3px;vertical-align:super;margin-left:6px}
.count{position:absolute;left:655px;top:250px;display:flex;gap:22px;align-items:flex-start}
.count div{text-align:center;font-size:25px;font-weight:600;color:#111;line-height:28px}
.count div small{display:block;font-size:10px;font-weight:400;letter-spacing:2px;color:#555}
.count .sep{font-size:22px}
.btn-blue{position:absolute;background:var(--blue);color:#fff;font-size:14px;font-weight:600;text-align:center;letter-spacing:.5px}
.quote{position:absolute;top:3582px;left:0;width:1200px;height:355px;background:linear-gradient(120deg,#2a2a2c,#1f1f22 50%,#2c2a2a);text-align:center;color:#eee}
.quote .mark{position:absolute;top:70px;left:0;width:100%;font-size:46px;color:var(--blue);font-weight:700}
.quote p{position:absolute;top:124px;left:275px;width:650px;font-size:13.5px;line-height:22px}
.quote .avatar{position:absolute;top:218px;left:578px;width:44px;height:44px;border-radius:50%;background:#b5544d;border:2px solid #fff}
.quote .who{position:absolute;top:268px;left:0;width:100%;font-size:11px}
.quote .who b{display:block;font-weight:600}
.dots{position:absolute;top:3969px;left:567px;display:flex;gap:11px}
.dots i{width:13px;height:13px;border-radius:50%;background:var(--blue)}
.dots i:first-child{background:#fff;border:2px solid var(--blue)}
.news h3{position:absolute;left:160px;top:4062px;font-size:24px;font-weight:400;color:var(--blue)}
.news p{position:absolute;left:160px;top:4100px;font-size:13.5px;color:#333}
.news .input{position:absolute;left:599px;top:4066px;width:289px;height:50px;border:1px solid #bbb;font-size:13px;color:#999;padding:14px 10px}
.blog-band{position:absolute;top:4212px;left:0;width:1200px;height:610px;background:var(--band)}
.post{position:absolute;top:4364px;width:240px}
.post .photo{position:relative;width:240px;height:164px}
.post .date{margin-top:20px;font-size:13px;color:var(--blue)}
.post h4{font-size:17px;font-weight:500;line-height:27px;color:#111;margin-top:2px}
.post .by{font-size:12px;color:#444;margin-top:2px}
.footer{position:absolute;top:4822px;left:0;width:1200px;height:535px;background:var(--footer);color:#ddd}
.footer h5{position:absolute;font-size:15px;font-weight:600;color:#fff}
.footer ul{position:absolute;list-style:none;font-size:15px;line-height:24px}
.footer .about{position:absolute;left:141px;top:128px;width:220px;font-size:15px;line-height:21px}
.footer .brand{position:absolute;left:141px;top:220px;font-size:28px;font-weight:600;color:#fff}
.footer .ci{position:absolute;left:871px;display:flex;gap:12px;font-size:15px;line-height:21px;align-items:flex-start}
.footer .email-in{position:absolute;left:141px;top:384px;width:198px;height:40px;background:#111;border:1px solid #333;font-size:13px;color:#ccc;padding:10px 14px}
.socials{position:absolute;left:893px;top:382px;display:flex;gap:24px}
.socials i{width:28px;height:28px;border-radius:50%;border:1px solid #555;background:#2a2a2c}
.socials i:first-child{border-color:var(--blue)}
.footer .bottom{position:absolute;left:0;top:473px;width:1200px;height:62px;background:var(--footer-bottom);font-size:11px;color:#ccc}
</style>
</head>
<body>

<header class="topbar">
  <div class="contact">
    <span><svg width="14" height="11" viewBox="0 0 14 11"><rect width="14" height="11" rx="1" fill="#444"/><path d="M1 1l6 5 6-5" stroke="#fff" fill="none"/></svg>hello@bolddawnapperal.com</span>
    <span><svg width="12" height="12" viewBox="0 0 24 24"><path fill="#444" d="M6.6 10.8a15 15 0 006.6 6.6l2.2-2.2c.3-.3.7-.4 1-.2 1.1.4 2.3.6 3.6.6.6 0 1 .4 1 1V20c0 .6-.4 1-1 1A17 17 0 013 4c0-.6.4-1 1-1h3.5c.6 0 1 .4 1 1 0 1.3.2 2.5.6 3.6.1.3 0 .7-.2 1z"/></svg>+01 555 204 318</span>
  </div>
  <div class="welcome">Welcome Visitor! <a>Log In</a> Or <a>Register</a></div>
</header>

<nav class="nav">
  <div class="brand">Bold Dawn</div>
  <div class="menu"><span class="active">HOME</span><span>ABOUT</span><span>KIDS</span><span>WOMEN</span><span>MAN</span><span>BLOG</span><span>CONTACT</span></div>
  <div class="search"><svg width="12" height="12" viewBox="0 0 12 12"><circle cx="5" cy="5" r="4" stroke="#777" fill="none" stroke-width="1.5"/><path d="M8 8l3 3" stroke="#777" stroke-width="1.5"/></svg>Search</div>
  <div class="cart"><svg width="24" height="22" viewBox="0 0 24 22"><path d="M1 2h4l3 12h12l3-9H6" stroke="#888" stroke-width="2" fill="none"/><circle cx="9" cy="19" r="2" fill="#888"/><circle cx="19" cy="19" r="2" fill="#888"/></svg><b>0</b></div>
</nav>

<section class="hero">
  <div class="photo" role="img" aria-label="Smiling woman in a yellow top holding colourful shopping bags"></div>
  <div class="kicker">IN STORES &amp; ONLINE NOW</div>
  <h1>Take Your Fit<br>to the Next Level</h1>
  <div class="btn-white">SHOP NOW</div>
</section>

<div class="features">
  <div class="feature">
    <svg width="48" height="40" viewBox="0 0 48 40"><rect x="2" y="8" width="28" height="22" rx="2" fill="none" stroke="var(--blue)" stroke-width="2"/><path d="M30 14h9l7 8v8H30z" fill="none" stroke="var(--blue)" stroke-width="2"/><circle cx="12" cy="33" r="4" fill="#fff" stroke="var(--blue)" stroke-width="2"/><circle cx="38" cy="33" r="4" fill="#fff" stroke="var(--blue)" stroke-width="2"/></svg>
    <div><h4>Free Shipping</h4><p>Free Shipping World Wide</p></div>
  </div>
  <div class="feature">
    <svg width="44" height="40" viewBox="0 0 44 40"><circle cx="24" cy="14" r="10" fill="none" stroke="var(--blue)" stroke-width="2"/><path d="M2 30c6-4 12-4 18 0h10l8-6" fill="none" stroke="var(--blue)" stroke-width="2"/></svg>
    <div><h4>Return Exchange</h4><p>30 Days Moneyback Grantee</p></div>
  </div>
  <div class="feature">
    <svg width="44" height="40" viewBox="0 0 44 40"><path d="M38 20a17 17 0 11-5-12" fill="none" stroke="var(--blue)" stroke-width="2"/><path d="M34 2v7h-7" fill="none" stroke="var(--blue)" stroke-width="2"/><path d="M21 10v10l6 4" fill="none" stroke="var(--blue)" stroke-width="2"/></svg>
    <div><h4>24/7 Service</h4><p>Online Service For New Customer</p></div>
  </div>
</div>

<div class="photo" style="left:179px;top:946px;width:478px;height:360px;background:linear-gradient(135deg,#e9e6e3,#c47a6a 45%,#5a6a7c 75%,#d8d4cf)" role="img" aria-label="Two women in sun hats and patterned dresses"></div>
<div class="photo" style="left:682px;top:946px;width:375px;height:273px;background:linear-gradient(160deg,#d7d4cd,#f2f1ef 55%,#b9b3a8)" role="img" aria-label="Woman in a black hat and white t-shirt"></div>
<div class="photo" style="left:682px;top:1248px;width:375px;height:270px;background:linear-gradient(135deg,#ec8fa7,#f3f0f0 55%,#eb8aa3)" role="img" aria-label="Woman in a white t-shirt on a pink background"></div>
<div class="coll-text">
  <div class="label">Hot Collection</div>
  <h2>New Trend For Women</h2>
  <p>Lorem ipsum dolor sit amet, consectetur adipiscing elit, sed do eiusmod tempor incididunt ut labore et dolore magna aliqua. Ut enim ad minim veniam, quis nostrud exercitation ullamco laboris.</p>
  <div class="btn-outline">SHOP NOW</div>
</div>

<h2 class="section-title" style="top:1622px">Featured Items</h2>
<div class="tabs"><span class="on">All</span><span>Men</span><span>Women</span><span>Kids</span></div>

<div class="product" style="left:160px;top:1745px"><div class="photo" style="background:linear-gradient(180deg,#4aa7ad,#e9e2cf 60%,#4aa7ad)" role="img" aria-label="Boy in white t-shirt with skateboard"></div><div class="cat">KIDS</div><div class="name">KIDS T-Shirt</div><div class="price">$108.08 <s>$124.52</s></div></div>
<div class="product" style="left:385px;top:1745px"><div class="photo" style="background:linear-gradient(180deg,#dcdad7,#2a2a2a 55%,#c9c6c1)" role="img" aria-label="Woman in black t-shirt"></div><div class="cat">WOMEN</div><div class="name">Womens T-Shirt</div><div class="price">$108.08 <s>$124.52</s></div></div>
<div class="product" style="left:609px;top:1745px"><div class="photo" style="background:linear-gradient(180deg,#ebe9e6,#f6f6f6 55%,#dcd9d4)" role="img" aria-label="Man in white t-shirt"><span class="badge">20%<br>OFF</span></div><div class="cat">MENS</div><div class="name">MEN T-Shirt</div><div class="price">$108.08 <s>$124.52</s></div></div>
<div class="product" style="left:834px;top:1745px"><div class="photo" style="background:linear-gradient(180deg,#545e66,#e8e8e8 55%,#4b545b)" role="img" aria-label="Child in bucket hat and sunglasses"></div><div class="cat">KIDS</div><div class="name">KIDS T-Shirt</div><div class="price">$108.08 <s>$124.52</s></div></div>

<div class="product" style="left:160px;top:2161px"><div class="photo" style="background:linear-gradient(180deg,#c8c2b8,#2b2b2b 50%,#6b8fb5)" role="img" aria-label="Man in black t-shirt seated"></div><div class="cat">MENS</div><div class="name">MEN T-Shirt</div><div class="price">$108.08 <s>$124.52</s></div></div>
<div class="product" style="left:385px;top:2161px"><div class="photo" style="background:linear-gradient(180deg,#6e6a63,#d23b3b 55%,#8a837a)" role="img" aria-label="Girl in red t-shirt"></div><div class="cat">KIDS</div><div class="name">KIDS T-Shirt</div><div class="price">$108.08 <s>$124.52</s></div></div>
<div class="product" style="left:609px;top:2161px"><div class="photo" style="background:linear-gradient(180deg,#c2434b,#f1f1f1 55%,#b33b44)" role="img" aria-label="Woman in white t-shirt on a city street"><span class="badge">20%<br>OFF</span></div><div class="cat">WOMEN</div><div class="name">Womens T-Shirt</div><div class="price">$108.08 <s>$124.52</s></div></div>
<div class="product" style="left:834px;top:2161px"><div class="photo" style="background:linear-gradient(180deg,#9a7a66,#f1ece4 55%,#7c6558)" role="img" aria-label="Toddler in printed sweatshirt"></div><div class="cat">KIDS</div><div class="name">KIDS T-Shirt</div><div class="price">$108.08 <s>$124.52</s></div></div>

<div class="promo" role="img" aria-label="Clothing rack promotion banner">
  <div class="left"><div class="big">70% <small>OFF</small></div><div class="sub">WOMENS<br>T-Shirt</div></div>
  <div class="right">LOREM IPSUM<br>DOLOR SIT</div>
</div>

<section class="deal">
  <div class="photo" role="img" aria-label="White and black t-shirts hanging on a wooden ladder beside palm leaves"></div>
  <div class="kicker">Print playsuit dress</div>
  <h2>Deal of the Week!</h2>
  <div class="pct">50%<sup>off</sup></div>
  <div class="count">
    <div>07<small>DAY</small></div><span class="sep">:</span>
    <div>23<small>HOURS</small></div><span class="sep">:</span>
    <div>28<small>MIN</small></div><span class="sep">:</span>
    <div>57<small>SEC</small></div>
  </div>
  <div class="btn-blue" style="left:655px;top:341px;width:198px;height:46px;line-height:46px">SHOP COLLECTION</div>
</section>

<section class="quote" aria-label="Customer testimonial">
  <div class="mark">&ldquo;</div>
  <p>"Lorem ipsum dolor sit amet, consectetur adipiscing elit, sed do eiusmod tempor incididunt ut labore et dolore magna aliqua. Ut enim ad minim veniam, quis nostrud exercitation ullamco laboris nisi ut aliquip ex ea commodo consequat."</p>
  <div class="avatar" role="img" aria-label="Customer portrait"></div>
  <div class="who"><b>Mara Holt</b>CEO Of Company</div>
</section>
<div class="dots"><i></i><i></i><i></i></div>

<section class="news">
  <h3>Sign up for newsletter</h3>
  <p>Subscribe to the weekly newsletter for all the latest updates</p>
  <div class="input">Your email</div>
  <div class="btn-blue" style="left:888px;top:4066px;width:150px;height:50px;line-height:50px;font-size:12px">SUBSCRIBE</div>
</section>

<div class="blog-band"></div>
<h2 class="section-title" style="top:4292px;color:var(--blue)">Blog</h2>
<article class="post" style="left:183px"><div class="photo" style="background:linear-gradient(135deg,#e8e4df,#e3a9a4 50%,#c9c3ba)" role="img" aria-label="Pastel garments on a clothing rail"></div><div class="date">4 June 2020</div><h4>Lorem ipsum dolor sit con sec adipiscing elit</h4><div class="by">by: John Doe , 2 Comment</div></article>
<article class="post" style="left:480px"><div class="photo" style="background:linear-gradient(135deg,#e9e9e9,#c85f5a 40%,#3b6aa0 70%,#e4e4e4)" role="img" aria-label="Patterned shirts on hangers"></div><div class="date">4 June 2020</div><h4>Lorem ipsum dolor sit con sec adipiscing elit</h4><div class="by">by: John Doe , 2 Comment</div></article>
<article class="post" style="left:799px"><div class="photo" style="background:linear-gradient(135deg,#d9cdc2,#b98a64 50%,#e6ddd3)" role="img" aria-label="Woman in a camel coat with a handbag"></div><div class="date">4 June 2020</div><h4>Lorem ipsum dolor sit con sec adipiscing elit</h4><div class="by">by: John Doe , 2 Comment</div></article>
<div class="btn-blue" style="left:535px;top:4684px;width:135px;height:48px;line-height:48px">VIEW ALL</div>

<footer class="footer">
  <h5 style="left:141px;top:95px">ABOUT US</h5>
  <div class="about">Lorem Ipsum is simply dummy text of the printing and typeset industry orem</div>
  <div class="brand">Bold Dawn</div>

  <h5 style="left:455px;top:93px">ALL MENU</h5>
  <ul style="left:455px;top:126px"><li>Kids</li><li>Women</li><li>Man</li><li>Blog</li><li>Contact</li></ul>

  <h5 style="left:653px;top:101px">ACCOUNT</h5>
  <ul style="left:653px;top:134px"><li>Sign in/ Sign Up</li><li>Dashboard</li><li>Track Order</li><li>Wishlist</li><li>Checkout</li></ul>

  <h5 style="left:871px;top:93px">CONTACT</h5>
  <div class="ci" style="top:132px"><svg width="14" height="14" viewBox="0 0 24 24"><path fill="var(--blue)" d="M6.6 10.8a15 15 0 006.6 6.6l2.2-2.2c.3-.3.7-.4 1-.2 1.1.4 2.3.6 3.6.6.6 0 1 .4 1 1V20c0 .6-.4 1-1 1A17 17 0 013 4c0-.6.4-1 1-1h3.5c.6 0 1 .4 1 1 0 1.3.2 2.5.6 3.6.1.3 0 .7-.2 1z"/></svg>0400 555 170</div>
  <div class="ci" style="top:176px"><svg width="14" height="11" viewBox="0 0 14 11"><rect width="14" height="11" rx="1" fill="var(--blue)"/><path d="M1 1l6 5 6-5" stroke="#fff" fill="none"/></svg>studio@bolddawnapperal.com</div>
  <div class="ci" style="top:210px"><svg width="12" height="16" viewBox="0 0 12 16"><path fill="var(--blue)" d="M6 0a6 6 0 016 6c0 4-6 10-6 10S0 10 0 6a6 6 0 016-6z"/><circle cx="6" cy="6" r="2" fill="#1f1f21"/></svg>House number, Lane or Road<br>Number, City, Zip Code</div>

  <h5 style="left:141px;top:340px">Subscribe To Us</h5>
  <div class="email-in">Enter email</div>
  <div class="btn-blue" style="left:339px;top:384px;width:102px;height:40px;line-height:40px;font-size:13px">SEND</div>

  <h5 style="left:890px;top:340px">Follow Us:</h5>
  <div class="socials"><i></i><i></i><i></i><i></i><i></i></div>

  <div class="bottom">
    <span class="abs" style="left:114px;top:24px">©copywrite. All right reserved by company name.</span>
    <span class="abs" style="right:80px;top:24px">Terms &amp; Condition, Privacy &amp; Policy</span>
  </div>
</footer>

</body>
</html>
```